Harbor Crest Holdings Corporate Showcase

Provide an attractive Corporate Website for a boutique Investment Company to showcase our activities and corporate interests.

Our Company works across a number of Sectors including

Real Estate
E-Commerce
Healthcare
Beauty & Personal Care
Technology
Resources

Lets keep the personality

Modern
Global
Sophisticated
Calm
Interesting

Lets keep the pages with MINIMAL Words
Lets use Photos/ Imagery to tell the story

We'll need a Banner Menu -
About Us
Expertise
Global Outlook
Sectors
Management
Media
Contact Us

Many thanks
Best wishes
Dennis.

Target Market(s)

Investors
Clients

Coding

Coded - Design and coding required

Number of Pages Required

5+ page

Font styles to use
Sans Serif

Colors
886aae
3176b5
00a990
f68e4d
f04a50
e667a6

Requirements
Must have
• WordPress Coding

Checkout this Website for look and feel - its cool:
www.qvr-example.com

Harbor Crest Partners
(Harbor Crest Holdings LLP)
London
E9 4ZX
United Kingdom

www.HarborCrestPartners-example.com
Nice to have
• Sophisticated colour palette - black/ brown/ blue/ purple/

```html
<!DOCTYPE html>
<html lang="en">
<head>
<meta charset="utf-8">
<title>Harbor Crest Holdings</title>
<link href="https://fonts.googleapis.com/css2?family=Lato:wght@400;700;900&display=swap" rel="stylesheet">
<style>
:root{
  --ink:#2b2b2b;
  --body:#444;
  --blue:#2f66b0;
  --blue-text:#2d5fa3;
  --teal:#1a9a80;
  --teal-text:#1a9a80;
  --purple:#7b4f9e;
  --red:#e03a45;
  --line:#a8a8a8;
  --white:#fff;
}
*{margin:0;padding:0;box-sizing:border-box}
html,body{width:1200px;height:3583px;overflow:hidden}
body{position:relative;font-family:'Lato',sans-serif;color:var(--body);background:var(--white)}
.abs{position:absolute}
.brand{left:75px;top:22px;font-size:29px;font-weight:700;line-height:33px;color:var(--ink)}
.phone{right:75px;top:40px;font-size:25px;font-weight:700;color:var(--teal-text);display:flex;align-items:center;gap:18px}
.nav{left:0;top:108px;width:1200px;height:66px;background:var(--blue);display:flex;justify-content:center;align-items:center;gap:37px}
.nav a{color:var(--white);text-decoration:none;font-size:17px;letter-spacing:.2px}
.hero{left:0;top:174px;width:1200px;height:562px;background:linear-gradient(135deg,#3b3a3c 0%,#7a6a5a 35%,#cdb89c 55%,#6b6a72 75%,#2c2b30 100%)}
.hero-title{left:0;top:372px;width:1200px;text-align:center;color:#fff;font-size:58px;font-weight:900;text-shadow:0 2px 6px rgba(0,0,0,.4)}
.hero-sub{left:300px;top:450px;width:600px;text-align:center;color:#fff;font-size:28px;font-weight:700;line-height:39px;text-shadow:0 2px 5px rgba(0,0,0,.4)}
.eyebrow{font-size:17px;font-weight:700;color:var(--blue-text)}
.h2{font-size:36px;font-weight:900;color:var(--ink)}
.center{text-align:center;width:1200px;left:0}
.sector{width:250px;text-align:center}
.sector svg{display:block;margin:0 auto}
.sector h3{font-size:21px;font-weight:700;color:var(--purple);margin-top:22px}
.sector p{font-size:14px;line-height:26px;color:var(--body);margin-top:10px}
.line{background:var(--line)}
.photo{}
.copy{width:515px}
.copy p{font-size:16px;line-height:33.3px;color:var(--body);margin-top:14px}
.btn{display:inline-block;width:164px;height:50px;line-height:50px;text-align:center;background:var(--teal);color:#fff;font-size:14px;font-weight:700;margin-top:38px}
.media{left:0;top:2758px;width:1200px;height:435px;background:linear-gradient(90deg,#7b539c 0%,#b24576 55%,#e8343f 100%)}
.media .eyebrow{color:#fff}
.media .h2{color:#fff}
.card-text{width:245px;color:#fff}
.card-text h4{font-size:21px;font-weight:700}
.card-text p{font-size:16px;line-height:28px;margin-top:6px;color:#f4e6ee}
.card-text a{display:block;font-size:17px;font-weight:700;color:#fff;margin-top:10px;text-decoration:none}
.foot-brand{left:75px;top:3255px;font-size:29px;font-weight:700;line-height:33px;color:var(--blue-text)}
.copyright{left:75px;top:3363px;font-size:12px;line-height:20px;color:#333}
.social{left:75px;top:3428px;display:flex;gap:22px}
.social span{width:20px;height:20px;border-radius:50%;background:#222;display:block}
.fcol h5{font-size:22px;font-weight:700;color:var(--ink);margin-bottom:6px}
.fcol a{display:block;font-size:16px;line-height:32.5px;color:#333;text-decoration:none}
.info{display:flex;gap:16px;font-size:16px;line-height:26px;color:#333;margin-bottom:12px;width:230px}
.info svg{flex:none;margin-top:5px}
</style>
</head>
<body>

<header>
  <div class="abs brand">Harbor Crest<br>Holdings</div>
  <div class="abs phone">
    <svg width="24" height="24" viewBox="0 0 24 24"><path fill="#e03a45" d="M6.6 10.8a15.2 15.2 0 0 0 6.6 6.6l2.2-2.2c.3-.3.7-.4 1-.2 1.1.4 2.3.6 3.6.6.6 0 1 .4 1 1V20c0 .6-.4 1-1 1A17 17 0 0 1 3 4c0-.6.4-1 1-1h3.5c.6 0 1 .4 1 1 0 1.3.2 2.5.6 3.6.1.3 0 .7-.2 1z"/></svg>
    1-800-555-0147
  </div>
  <nav class="abs nav">
    <a href="#">HOME</a><a href="#">ABOUT US</a><a href="#">EXPERTISE</a><a href="#">GLOBAL OUTLOOK</a><a href="#">SECTORS</a><a href="#">MANAGEMENT</a><a href="#">MEDIA</a><a href="#">CONTACT US</a>
  </nav>
</header>

<section>
  <div class="abs hero" role="img" aria-label="Overhead view of business people shaking hands across a desk with charts, laptop and coffee"></div>
  <h1 class="abs hero-title">Harbor Crest Holdings</h1>
  <p class="abs hero-sub">Nam libero tempore, cum soluta nobis est eligendi optio cumque nihil.</p>
</section>

<section>
  <div class="abs center eyebrow" style="top:817px">WHAT WE DO</div>
  <h2 class="abs center h2" style="top:842px">OUR SECTORS</h2>

  <div class="abs sector" style="left:70px;top:922px">
    <svg width="60" height="62" viewBox="0 0 60 62" fill="none" stroke="#e03a45" stroke-width="2"><path d="M4 60h52M10 60V8l20-6v58M30 22h20v38M16 14h4M22 14h4M16 24h4M22 24h4M16 34h4M22 34h4M16 44h4M22 44h4M36 30h4M44 30h4M36 40h4M44 40h4M36 50h4M44 50h4"/></svg>
    <h3>Real Estate</h3>
    <p>At vero eos et accusamus et iusto odio dignissimos ducimus qui culpa qui officia.</p>
  </div>
  <div class="abs sector" style="left:340px;top:922px">
    <svg width="68" height="62" viewBox="0 0 68 62" fill="none" stroke="#e03a45" stroke-width="2"><rect x="2" y="2" width="64" height="46" rx="3"/><path d="M2 12h64M8 7h2M13 7h2M18 7h2M14 20h6l6 16h24l5-12H24M28 36l-2 6h26"/><circle cx="30" cy="48" r="3"/><circle cx="48" cy="48" r="3"/></svg>
    <h3>E-Commerce</h3>
    <p>At vero eos et accusamus et iusto odio dignissimos ducimus qui culpa qui officia.</p>
  </div>
  <div class="abs sector" style="left:610px;top:922px">
    <svg width="76" height="62" viewBox="0 0 76 62" fill="none" stroke="#e03a45" stroke-width="2"><path d="M38 38c-8-6-12-10-12-15a6 6 0 0 1 12-2 6 6 0 0 1 12 2c0 5-4 9-12 15z"/><path d="M4 40l12-10h10l10 6M72 22L60 32H50l-8-4M20 54l10-8M56 8l-10 8"/></svg>
    <h3>Healthcare</h3>
    <p>At vero eos et accusamus et iusto odio dignissimos ducimus qui culpa qui officia.</p>
  </div>
  <div class="abs sector" style="left:880px;top:922px">
    <svg width="64" height="62" viewBox="0 0 64 62" fill="none" stroke="#e03a45" stroke-width="2"><rect x="6" y="38" width="34" height="20" rx="2"/><path d="M6 46h34M23 38V30M23 20c-4 4-4 8 0 10 4-2 4-6 0-10zM46 58V30M46 30c-6-2-8-10-6-18l6 6 6-6c2 8 0 16-6 18zM6 10l2 2M10 4v3M40 30l-4-4M52 34l4-4"/></svg>
    <h3>Beauty &amp; Personal Care</h3>
    <p>At vero eos et accusamus et iusto odio dignissimos ducimus qui culpa qui officia.</p>
  </div>
</section>

<!-- connectors -->
<div class="abs line" style="left:601px;top:1165px;width:2px;height:28px"></div>
<div class="abs line" style="left:328px;top:1191px;width:275px;height:2px"></div>
<div class="abs line" style="left:328px;top:1191px;width:2px;height:53px"></div>

<section>
  <div class="abs photo" style="left:75px;top:1244px;width:511px;height:410px;background:linear-gradient(120deg,#c9cfd6,#3a4a6a 55%,#20304f)" role="img" aria-label="Two business colleagues in suits discussing a document in an office"></div>
  <div class="abs copy" style="left:616px;top:1266px">
    <div class="eyebrow">WHO WE ARE</div>
    <h2 class="h2" style="line-height:40px">ABOUT US</h2>
    <p>At vero eos et accusamus et iusto odio dignissimos ducimus qui blanditiis praesentium voluptatum deleniti atque corrupti quos dolores et quas molestias excepturi sint occaecati cupiditate non provident, similique sunt in culpa qui officia deserunt mollitia animi harum quidem rerum facilis est et expedita distinctio.nam libero tempore, cum soluta nobis est.</p>
    <a class="btn" href="#">READ MORE</a>
  </div>
</section>

<div class="abs line" style="left:328px;top:1654px;width:2px;height:62px"></div>
<div class="abs line" style="left:328px;top:1715px;width:543px;height:2px"></div>
<div class="abs line" style="left:869px;top:1715px;width:2px;height:46px"></div>

<section>
  <div class="abs photo" style="left:616px;top:1761px;width:511px;height:410px;background:linear-gradient(160deg,#8fb0cf,#4f6f95 50%,#2d3d55)" role="img" aria-label="Coin-operated viewing binoculars overlooking mountains"></div>
  <div class="abs copy" style="left:75px;top:1792px">
    <h2 class="h2" style="line-height:40px">GLOBAL OUTLOOK</h2>
    <p>At vero eos et accusamus et iusto odio dignissimos ducimus qui blanditiis praesentium voluptatum deleniti atque corrupti quos dolores et quas molestias excepturi sint occaecati cupiditate non provident, similique sunt in culpa qui officia deserunt mollitia animi harum quidem rerum facilis est et expedita distinctio.nam libero tempore, cum soluta nobis est.</p>
    <a class="btn" href="#">READ MORE</a>
  </div>
</section>

<div class="abs line" style="left:869px;top:2171px;width:2px;height:48px"></div>
<div class="abs line" style="left:328px;top:2217px;width:543px;height:2px"></div>
<div class="abs line" style="left:328px;top:2217px;width:2px;height:59px"></div>

<section>
  <div class="abs photo" style="left:75px;top:2276px;width:511px;height:410px;background:linear-gradient(150deg,#e8ecef,#c9d1d8 50%,#8a7a68)" role="img" aria-label="Person at a desk pointing at a project timeline on a computer monitor"></div>
  <div class="abs copy" style="left:616px;top:2312px">
    <h2 class="h2" style="line-height:40px">MANAGEMENT</h2>
    <p>At vero eos et accusamus et iusto odio dignissimos ducimus qui blanditiis praesentium voluptatum deleniti atque corrupti quos dolores et quas molestias excepturi sint occaecati cupiditate non provident, similique sunt in culpa qui officia deserunt mollitia animi harum quidem rerum facilis est et expedita distinctio.nam libero tempore, cum soluta nobis est.</p>
    <a class="btn" href="#">READ MORE</a>
  </div>
</section>

<section class="abs media">
  <div class="abs center eyebrow" style="top:69px">LATEST UPDATES</div>
  <h2 class="abs center h2" style="top:92px">MEDIA</h2>

  <div class="abs" style="left:75px;top:173px;width:242px;height:187px;background:linear-gradient(135deg,#d5d9de,#7d8794 60%,#3c4450)" role="img" aria-label="Hands pointing at financial charts beside a laptop"></div>
  <div class="abs card-text" style="left:342px;top:178px">
    <h4>At vero eos et accusamus</h4>
    <p>Dignissimos ducimus qui blanditiis praesentium voluptatum deleniti atque corrupti quos.</p>
    <a href="#">Read More</a>
  </div>

  <div class="abs" style="left:616px;top:173px;width:242px;height:187px;background:linear-gradient(135deg,#e6e8ea,#9aa3ad 55%,#3a3f48)" role="img" aria-label="Two businessmen reviewing work on a laptop"></div>
  <div class="abs card-text" style="left:883px;top:178px">
    <h4>At vero eos et accusamus</h4>
    <p>Dignissimos ducimus qui blanditiis praesentium voluptatum deleniti atque corrupti quos.</p>
    <a href="#">Read More</a>
  </div>
</section>

<footer>
  <div class="abs foot-brand">Harbor Crest<br>Holdings</div>
  <div class="abs copyright">Copyright © 2020. Company Name<br>All Right Reserved</div>
  <div class="abs social" aria-label="Social links"><span></span><span></span><span></span><span></span><span></span><span></span></div>

  <div class="abs fcol" style="left:364px;top:3256px">
    <h5>Site Map</h5>
    <a href="#">Home</a><a href="#">About Us</a><a href="#">Expertise</a><a href="#">Global Outlook</a><a href="#">Sectors</a><a href="#">Management</a><a href="#">Media</a><a href="#">Contact Us</a>
  </div>
  <div class="abs fcol" style="left:627px;top:3256px">
    <h5>Sectors</h5>
    <a href="#">Real Estate</a><a href="#">E-Commerce</a><a href="#">Healthcare</a><a href="#">Beauty &amp; Personal Care</a><a href="#">Technology</a><a href="#">Resources</a>
  </div>
  <div class="abs fcol" style="left:899px;top:3256px">
    <h5 style="margin-bottom:12px">Company Info</h5>
    <div class="info"><svg width="18" height="16" viewBox="0 0 18 16"><path fill="#333" d="M0 3l5-2 6 2 6-2v12l-6 2-6-2-5 2z"/></svg><span>Cum sociis natoque penatibus</span></div>
    <div class="info"><svg width="16" height="16" viewBox="0 0 24 24"><path fill="#333" d="M6.6 10.8a15.2 15.2 0 0 0 6.6 6.6l2.2-2.2c.3-.3.7-.4 1-.2 1.1.4 2.3.6 3.6.6.6 0 1 .4 1 1V20c0 .6-.4 1-1 1A17 17 0 0 1 3 4c0-.6.4-1 1-1h3.5c.6 0 1 .4 1 1 0 1.3.2 2.5.6 3.6.1.3 0 .7-.2 1z"/></svg><span>1-800-555-0147</span></div>
    <div class="info" style="width:260px"><svg width="16" height="16" viewBox="0 0 16 16"><rect x="1" y="3" width="14" height="11" rx="1" fill="#333"/><path d="M2 4l6 5 6-5" stroke="#fff" fill="none"/></svg><span>info@harborcrest-example.com</span></div>
  </div>
</footer>

</body>
</html>
```